Catering Menu Package

I currently have a complete menu package, which we have redesigned as far as content, now I need to it put together in a catalog type format. It is essentially 10-12 pages in length, and will be sent for print production. Upon receiving a final edit
Updates

I have added an example gif to the project.

I did this free hand this basically what I am looking for. please change text and type to whatever you think would look best. This is a total rough design so, feel free to change any and everything. The text for the page is on the word documents. If you need more images let me know I am in the process of getting as many images uploaded for your use.

Project Deadline Extended
Reason: I figured we got a late jump with questions, so i am extending a few days .

Target Market(s)

The target market is business who wish to have catered luncheons, breakfasts , meetings

Industry/Entity Type

Catering

Requirements
Must have
• I have attached a copy of the text that what we want in the package, our logo, and i have also attached a catering package of another company to give you an idea what the finished product will be
Should not have
• It should not look identical to the example catering packages, these are for some inspiration we want our own design with the same type of look and feel

```html
<!DOCTYPE html>
<html lang="en">
<head>
<meta charset="utf-8">
<title>Cocktail Hour and Reception Menus</title>
<link rel="stylesheet" href="https://fonts.googleapis.com/css2?family=Fondamento&family=Lora:ital,wght@1,400;1,700&family=Gelasio:wght@700&display=swap">
<style>
:root{
  --backdrop:#ece7df;
  --paper:#e6ded2;
  --orange:#f07a26;
  --orange-text:#ef7b2a;
  --green:#6cbd4f;
  --ink:#111;
  --white:#fff;
  --logo-ink:#1e1e1e;
}
*{box-sizing:border-box;margin:0;padding:0}
html,body{width:1200px;height:800px;overflow:hidden;background:var(--backdrop)}
.canvas{position:relative;width:1200px;height:800px}
.page{position:absolute;top:15px;width:565px;height:747px;background:var(--paper);overflow:hidden;box-shadow:0 2px 8px rgba(0,0,0,.25)}
.page--front{left:22px}
.page--back{left:608px}
.photo{position:absolute;inset:0}
.title-banner{position:absolute;left:0;top:10px;width:420px;height:60px}
.title-banner__rule{position:absolute;left:18px;right:0;top:30px;height:5px;background:var(--orange)}
.title-banner__box{position:absolute;left:78px;width:280px;height:60px;background:var(--orange);color:var(--white);font:italic 700 19px/25px "Lora",serif;text-align:center;padding-top:5px}
.menu-title{position:absolute;font:32px/40px "Fondamento",serif;color:var(--orange-text);text-align:center;width:420px;left:0}
.menu-subtitle{position:absolute;left:10px;width:420px;top:47px;font:italic 700 15px/16px "Lora",serif;color:var(--ink);text-align:center}
.item{position:absolute;font:italic 400 16px/18px "Lora",serif;color:var(--orange-text)}
.price{position:absolute;font:700 17px/18px "Gelasio",serif;color:var(--ink)}
.note{position:absolute;left:12px;top:657px;width:398px;height:29px;border-radius:10px;background:var(--green);color:var(--white);font:9.5px/12px "Gelasio",Georgia,serif;font-weight:400;text-align:center;padding-top:3px}
.contact-band{position:absolute;left:0;top:688px;width:418px;height:47px;background:var(--orange);color:var(--white)}
.contact-band__cta{position:absolute;left:18px;top:4px;font:italic 10px/12px "Lora",serif}
.contact-band__phone{position:absolute;left:30px;top:17px;font:italic 700 20px/24px "Lora",serif;display:flex;align-items:center;gap:6px}
.contact-band__address{position:absolute;left:232px;top:6px;font:10px/13px Georgia,serif}
.brand-box{position:absolute;left:418px;top:520px;width:147px;height:227px;background:var(--white);display:flex;flex-direction:column;align-items:center;justify-content:center;gap:14px}
.brand-box__mark{width:46px;height:46px;border-radius:50%;background:var(--orange)}
.brand-box__name{font:italic 700 19px/22px "Lora",serif;color:var(--logo-ink);text-align:center}
</style>
</head>
<body>
<div class="canvas">

  <section class="page page--front">
    <svg class="photo" width="565" height="747" viewBox="0 0 565 747" role="img" aria-label="Glazed chicken wings with ranch dip and celery sticks">
      <defs>
        <linearGradient id="wingsTone" x1="0" y1="0" x2="0" y2="1">
          <stop offset="0" stop-color="#f4f1ec"/>
          <stop offset=".15" stop-color="#a8431f"/>
          <stop offset=".4" stop-color="#c96a3c"/>
          <stop offset=".55" stop-color="#eeeeea"/>
          <stop offset=".72" stop-color="#b5c98a"/>
          <stop offset="1" stop-color="#f2f2ee"/>
        </linearGradient>
      </defs>
      <path d="M466 0 Q440 260 415 520 L565 520 L565 0 Z" fill="url(#wingsTone)"/>
    </svg>

    <div class="title-banner">
      <div class="title-banner__rule"></div>
      <div class="title-banner__box">Sample Cocktail Hour and<br>Reception Menus</div>
    </div>
    <h1 class="menu-title" style="top:76px">The Sampler</h1>

    <div class="item" style="left:18px;top:129px">Assorted Miniature Sandwiches</div><div class="price" style="left:336px;top:129px">$&amp;.&amp;&amp;</div>
    <div class="item" style="left:18px;top:163px">Oven Roasted Turkey, Black Forest Ham &amp; Roasted<br>Top Round of Beef</div><div class="price" style="left:336px;top:187px">$&amp;.&amp;&amp;</div>
    <div class="item" style="left:18px;top:222px">Served on Artisan rolls &amp; fresh baked baguette</div><div class="price" style="left:336px;top:242px">$&amp;.&amp;&amp;</div>
    <div class="item" style="left:18px;top:272px">Served with Mayonaise, Mustard, Dijon, And<br>Horseradish</div><div class="price" style="left:336px;top:290px">$&amp;.&amp;&amp;</div>
    <div class="item" style="left:18px;top:328px">Rotisserie Roasted Chicken Drummies &amp; Wing<br>Sections</div><div class="price" style="left:336px;top:345px">$&amp;.&amp;&amp;</div>
    <div class="item" style="left:15px;top:380px">Served with sweet &amp; sour, hot sauce &amp; chipotle ranch</div><div class="price" style="left:336px;top:403px">$&amp;.&amp;&amp;</div>
    <div class="item" style="left:16px;top:437px">With celery and carrot stalks</div><div class="price" style="left:333px;top:437px">$&amp;.&amp;&amp;</div>
    <div class="item" style="left:16px;top:479px">Cranberry BBQ Meatballs</div><div class="price" style="left:333px;top:479px">$&amp;.&amp;&amp;</div>
    <div class="item" style="left:16px;top:522px">Fresh Fruit &amp; Melon Display</div><div class="price" style="left:333px;top:522px">$&amp;.&amp;&amp;</div>
    <div class="item" style="left:16px;top:561px">Vegetable Pasta Salad</div><div class="price" style="left:333px;top:561px">$&amp;.&amp;&amp;</div>
    <div class="item" style="left:16px;top:604px">Maryland Crab Dip</div><div class="price" style="left:333px;top:604px">$&amp;.&amp;&amp;</div>
    <div class="item" style="left:16px;top:636px">Served with Gourmet Crackers</div><div class="price" style="left:333px;top:636px">$&amp;.&amp;&amp;</div>

    <p class="note">All Prices are per Person, with a 10 person minimum order per item chosen.<br>Local Products used when available and in season</p>
    <div class="contact-band">
      <div class="contact-band__cta">CALL OR EMAIL US TODAY:</div>
      <div class="contact-band__phone"><svg width="22" height="18" viewBox="0 0 22 18" aria-hidden="true"><path d="M2 6 Q11 -1 20 6 L17 9 L14 6 L8 6 L5 9 Z M5 10 H17 L19 17 H3 Z" fill="#111"/></svg>410-555-0148</div>
      <div class="contact-band__address">218 Harlow Lane<br>Brenton, MD 20900<br>www.tidewatertable.com</div>
    </div>
    <div class="brand-box">
      <div class="brand-box__mark"></div>
      <div class="brand-box__name">Tidewater<br>Table<br>Caterers</div>
    </div>
  </section>

  <section class="page page--back">
    <svg class="photo" width="565" height="747" viewBox="0 0 565 747" role="img" aria-label="Bunch of fresh green grapes">
      <defs>
        <radialGradient id="grapeTone" cx=".6" cy=".4" r=".7">
          <stop offset="0" stop-color="#dbe79a"/>
          <stop offset=".6" stop-color="#b9cd6a"/>
          <stop offset="1" stop-color="#f3f5ea"/>
        </radialGradient>
      </defs>
      <path d="M427 0 Q480 260 427 520 L565 520 L565 0 Z" fill="url(#grapeTone)"/>
    </svg>

    <h1 class="menu-title" style="top:7px;left:-10px">The Artisan</h1>
    <p class="menu-subtitle">An Artfully Displayed Hors'doeuvre Table<br>including the following:</p>

    <div class="item" style="left:25px;top:100px">Artisan Rolls and Breads Lavosh, Assorted<br>Gourmet Crackers, and Crostinis Pita Bread Wedges<br>and&nbsp; Baguette Loafs</div><div class="price" style="left:343px;top:137px">$&amp;.&amp;&amp;</div>
    <div class="item" style="left:25px;top:175px">Fresh Grapes and Strawberries</div><div class="price" style="left:343px;top:175px">$&amp;.&amp;&amp;</div>
    <div class="item" style="left:25px;top:207px">Seasonal fruit</div><div class="price" style="left:343px;top:210px">$&amp;.&amp;&amp;</div>
    <div class="item" style="left:25px;top:244px">Garden Fresh Vegetables</div><div class="price" style="left:343px;top:244px">$&amp;.&amp;&amp;</div>
    <div class="item" style="left:25px;top:286px">Grilled and marinated in Aged Imported Balsamic<br>Vinegar.</div><div class="price" style="left:343px;top:303px">$&amp;.&amp;&amp;</div>
    <div class="item" style="left:25px;top:345px;line-height:20.5px">A Variety of Artesian Cheeses, including but not<br>&nbsp;limited Cheddar, Havarti, Goat Cheese,Gorgonzola,<br>Smoked Gouda, Pepper-Jack, and Brie accompanied<br>with assorted dried fruit and nuts.</div><div class="price" style="left:343px;top:411px">$&amp;.&amp;&amp;</div>
    <div class="item" style="left:23px;top:455px">Various Imported Olives and Pickled Vegetables</div><div class="price" style="left:340px;top:477px">$&amp;.&amp;&amp;</div>
    <div class="item" style="left:25px;top:521px">Aged Salami, Italian Hams, and Pepperoni.</div><div class="price" style="left:340px;top:539px">$&amp;.&amp;&amp;</div>
    <div class="item" style="left:24px;top:574px">Hummus and Olive Tapenades</div><div class="price" style="left:340px;top:574px">$&amp;.&amp;&amp;</div>
    <div class="item" style="left:24px;top:612px">Infused Olive Oils</div><div class="price" style="left:340px;top:612px">$&amp;.&amp;&amp;</div>

    <p class="note">All Prices are per Person, with a 10 person minimum order per item chosen.<br>Local Products used when available and in season</p>
    <div class="contact-band">
      <div class="contact-band__cta">CALL OR EMAIL US TODAY:</div>
      <div class="contact-band__phone"><svg width="22" height="18" viewBox="0 0 22 18" aria-hidden="true"><path d="M2 6 Q11 -1 20 6 L17 9 L14 6 L8 6 L5 9 Z M5 10 H17 L19 17 H3 Z" fill="#111"/></svg>410-555-0148</div>
      <div class="contact-band__address">218 Harlow Lane<br>Brenton, MD 20900<br>www.tidewatertable.com</div>
    </div>
    <div class="brand-box">
      <div class="brand-box__mark"></div>
      <div class="brand-box__name">Tidewater<br>Table<br>Caterers</div>
    </div>
  </section>

</div>
</body>
</html>
```